New Menu Design for edgy barbershop (with bar)

We have a basic graphic for a brand new membership menu. The menu will be located on the wall in our lobby area -- we are planning on making this a very large graphic, but I don't have exact dimensions.

We are a barbershop with a bar & the hottest lady barbers around. We strive to keep a western / saloon feel throughout the barbershop. We cater to mostly a male clientele, so want to have a masculine feel to any creative additions.

I have attached the graphic we started with -- we want to keep the general set up and flow, but are open to your creative brilliance! Our logo is also attached & you can get a good feel for our style on our website: www.brindlepost.com or on our Chatterwall page: www.facebook.com/brindlepost.

Let me know if you have any questions, or if you need more detail on any of these elements!

A few key details:
- All designs should be horizontal
- The main focus is on the memberships. We want these to pop, and wow customers -- attention should focus on memberships in the graphic, draw the eye in and look glorious.
- We won't look at designs that are too busy or cluttered. Needs to be easy to read & not overwhelming (even with all the information)
- Not too keen on background imagery or color splashes as these make it too complicated. The visual interest should be in how awesome the memberships are!
- Needs to have a clean, masculine feel. Less is more with the background graphics & focus is on getting the info out and drawing people into the awesome memberships we sell.

Target Market(s)

Men 21-65

Font styles to use
Sans Serif

Requirements
Must have
• Masculine feel, western / Saloon theme. Must have all the info included in the graphic slide.
• - Must be Horizontal
• - Must focus on the memberships (need to make the "wow" and drive people to buy them.
Nice to have
• Additional creative elements that really showcase the memberships as awesome!
Should not have
• - No vertical layouts
• - Overly added graphics or background imagery

```html
<!DOCTYPE html>
<html lang="en">
<head>
<meta charset="utf-8">
<title>Brindle Post — Membership Menu</title>
<link href="https://fonts.googleapis.com/css2?family=Ultra&family=Josefin+Slab:wght@400;600;700&family=Montserrat:wght@600;700&display=swap" rel="stylesheet">
<style>
:root{
  --ink:#1c1c1c;
  --orange:#e8762c;
  --paper:#ffffff;
  --frame:#111111;
  --muted:#555555;
}
*{margin:0;padding:0;box-sizing:border-box}
html,body{width:1200px;height:943px;overflow:hidden;background:var(--paper)}
.menu{position:relative;width:1200px;height:943px;background:var(--paper);border:10px solid var(--frame);color:var(--ink);font-family:'Montserrat',sans-serif}
.heavy{font-family:'Ultra',serif;font-weight:400;letter-spacing:1px;line-height:.95}
.light{font-family:'Josefin Slab',serif;font-weight:400;line-height:.95}
.price{font-family:'Josefin Slab',serif;font-weight:700;color:var(--orange);font-size:21px}
.desc{font-size:9.5px;font-weight:700;text-transform:uppercase;line-height:1.45;letter-spacing:.3px}
.item{position:absolute}
.rule{border-top:1px solid var(--ink);margin:3px 0 5px}
.wide{letter-spacing:7px}

.brand{position:absolute;left:0;right:0;top:42px;text-align:center}
.brand-name{font-family:'Ultra',serif;color:var(--orange);font-size:30px;letter-spacing:2px;display:inline-flex;align-items:center;gap:10px}
.brand-dot{width:14px;height:14px;background:var(--orange);border-radius:50%;display:inline-block}

.membership{position:absolute;left:636px;top:80px;width:510px;height:600px}
.membership svg{position:absolute;left:0;top:0}
.step{position:absolute;left:0;width:510px;text-align:center;color:var(--ink)}
.step small{display:block;font-size:7px;font-weight:700;letter-spacing:1px}
.step strong{display:block;font-size:12px;font-weight:700;letter-spacing:3px}
.svc,.extra{position:absolute;color:var(--paper);font-family:'Ultra',serif;text-align:center}
.extra small{display:block;font-family:'Montserrat',sans-serif;font-size:10px;font-weight:600;letter-spacing:1px}

.perks-title{position:absolute;left:646px;width:500px;top:690px;text-align:center}
.perks-title .the{font-family:'Josefin Slab',serif;font-size:17px}
.perks-title .big{font-family:'Ultra',serif;color:var(--orange);font-size:24px;letter-spacing:1px}
.perks-title small{display:block;font-family:'Josefin Slab',serif;font-size:9px;letter-spacing:1px}
.perks{position:absolute;left:646px;top:748px;width:500px;height:142px}
.perks ul{position:absolute;left:0;top:46px;width:500px;list-style:none;text-align:center;font-size:11.5px;font-weight:700;line-height:22px;text-transform:uppercase}
</style>
</head>
<body>
<main class="menu">

  <header class="brand">
    <span class="brand-name"><span class="brand-dot"></span>BRINDLE POST</span>
  </header>

  <!-- Column one -->
  <section class="item" style="left:48px;top:118px;width:210px">
    <div style="display:flex;gap:6px">
      <div style="width:76px;text-align:center">
        <div class="light" style="font-size:26px">THE</div>
        <div class="heavy" style="font-size:24px">COW<br>BOY</div>
        <div class="light" style="font-size:26px">CUT</div>
      </div>
      <div style="flex:1">
        <div class="price" style="text-align:right">$25</div>
        <div class="rule"></div>
        <p class="desc">Our full service cut. Hair cut, hot towel, double trough wash, and straight razor neck shave.</p>
      </div>
    </div>
  </section>

  <section class="item" style="left:48px;top:242px;width:210px">
    <div class="light" style="font-size:22px">THE</div>
    <div style="display:flex;justify-content:space-between;align-items:baseline">
      <span class="heavy wide" style="font-size:24px">TERRY</span><span class="price">$17</span>
    </div>
    <div class="rule"></div>
    <p class="desc">Haircut, double trough wash, hot towel, and straight razor neck shave.<br>This is for cowboys<br>that haven't been blessed<br>with a full head of hair.<br>We know it's not fair,<br>that's why your price is!</p>
  </section>

  <section class="item" style="left:48px;top:443px;width:210px">
    <div class="light" style="font-size:25px">THE</div>
    <div style="display:flex;justify-content:space-between;align-items:baseline">
      <span class="heavy wide" style="font-size:24px">LITTLE</span><span class="price">$15</span>
    </div>
    <div style="background:var(--ink);color:var(--paper);font-family:'Ultra',serif;font-size:12px;letter-spacing:2px;text-align:center;padding:2px 0;margin:3px 0 7px">COWBOY AND COWGIRL</div>
    <p class="desc">Kids cuts 14 and under hair cut, trough wash, and neck trim.</p>
  </section>

  <section class="item" style="left:48px;top:580px;width:210px">
    <div class="light" style="font-size:25px">THE</div>
    <div class="heavy wide" style="font-size:24px">SCALP</div>
    <div style="display:flex;justify-content:space-between;align-items:baseline">
      <span class="heavy wide" style="font-size:24px">SCRAPE</span><span class="price">$30</span>
    </div>
    <div class="rule"></div>
    <p class="desc">We will take a not so rusty<br>straight razor and get rid<br>of your carrot top.</p>
  </section>

  <section class="item" style="left:48px;top:740px;width:140px">
    <div class="price">$10</div>
    <div class="heavy" style="font-size:24px">ROUGH<br>RIDER</div>
    <div class="rule"></div>
    <p class="desc">Straight razor back of the neck shave &amp; two beers to keep your trail rides smooth.</p>
  </section>

  <section class="item" style="left:208px;top:740px;width:140px;text-align:center">
    <div class="price">$10</div>
    <div class="light" style="font-size:18px">THE</div>
    <div class="heavy" style="font-size:24px">COLO<br>RADO</div>
    <div class="rule"></div>
    <p class="desc">Electric trim<br>your man bush (beard)<br>just how you like it!</p>
  </section>

  <!-- Column two -->
  <section class="item" style="left:308px;top:118px;width:242px">
    <div style="display:flex;gap:8px">
      <div style="width:88px">
        <div class="price">$25</div>
        <div class="rule"></div>
        <p class="desc" style="text-align:right;font-size:8.5px">Our ladies cut. Hair cut, trough wash.</p>
      </div>
      <div>
        <div class="light" style="font-size:26px">THE</div>
        <div class="heavy" style="font-size:23px">COWGIRL</div>
        <div class="light" style="font-size:26px">CUT</div>
      </div>
    </div>
  </section>

  <section class="item" style="left:308px;top:242px;width:242px">
    <div class="light wide" style="font-size:24px;text-align:right;letter-spacing:3px">BUZZED</div>
    <div style="display:flex;justify-content:space-between;align-items:baseline">
      <span class="price">$22</span><span class="heavy" style="font-size:25px;letter-spacing:4px">COWBOY</span>
    </div>
    <div class="rule"></div>
    <p class="desc" style="font-size:8.5px">Buzz cut &amp; two beers, for the straight-forward cowboy. Must be 21+ for this bad boy.</p>
  </section>

  <section class="item" style="left:308px;top:360px;width:242px">
    <div style="display:flex;gap:8px">
      <div style="width:88px;padding-top:4px">
        <div class="price">$35</div>
        <div class="rule"></div>
        <p class="desc" style="text-align:right;font-size:8.5px">Cowboy and little cowboy hair cut.</p>
      </div>
      <div>
        <div class="light" style="font-size:20px">THE</div>
        <div class="heavy" style="font-size:24px">COWBOY<br>PACK</div>
      </div>
    </div>
  </section>

  <section class="item" style="left:308px;top:480px;width:242px">
    <div style="display:flex;gap:8px">
      <div style="width:88px;padding-top:2px">
        <div class="price">$30</div>
        <div class="rule"></div>
        <p class="desc" style="text-align:right;font-size:8.5px">Razor fade,<br>hot towel,<br>double wash.</p>
      </div>
      <div>
        <div class="light" style="font-size:19px">COWBOY</div>
        <div class="heavy wide" style="font-size:24px">RAZOR<br>FADE</div>
      </div>
    </div>
  </section>

  <section class="item" style="left:308px;top:580px;width:242px">
    <div class="light" style="font-size:25px;text-align:right">THE</div>
    <div class="heavy" style="font-size:24px;text-align:right;letter-spacing:3px">DOUBLE</div>
    <div style="display:flex;justify-content:space-between;align-items:baseline">
      <span class="price">$30</span><span class="heavy wide" style="font-size:24px">SCRAPE</span>
    </div>
    <div class="rule"></div>
    <p class="desc" style="text-align:right">We will take a not so rusty straight razor and get rid of your winter scruff. A face shave with and against the grain.</p>
  </section>

  <section class="item" style="left:398px;top:740px;width:152px;text-align:right">
    <div class="price">$10</div>
    <div class="light" style="font-size:26px;letter-spacing:2px">EYEBROW</div>
    <div class="heavy wide" style="font-size:24px;letter-spacing:4px">WAX</div>
    <div class="rule"></div>
    <p class="desc">We can wax them<br>both off, one off,<br>or just touch them up.<br>Add on to any cut.</p>
  </section>

  <!-- Membership panel -->
  <section class="membership" aria-label="Membership builder">
    <svg width="510" height="600" viewBox="0 0 510 600">
      <polygon points="50,60 460,60 500,100 500,560 460,600 50,600 10,560 10,100" fill="#e8762c" transform="translate(0,-8) scale(1,0.99)"/>
      <polygon points="54,66 456,66 494,104 494,556 456,586 54,586 16,556 16,104" fill="none" stroke="#1c1c1c" stroke-width="2"/>
      <circle cx="255" cy="58" r="46" fill="#ffffff"/>
      <circle cx="255" cy="58" r="40" fill="#1c1c1c"/>
      <circle cx="255" cy="58" r="30" fill="none" stroke="#e8762c" stroke-width="3"/>
      <rect x="28" y="92" width="36" height="28" rx="6" fill="#1c1c1c" role="img" aria-label="Cowboy hat icon"/>
      <rect x="446" y="92" width="36" height="28" rx="6" fill="#1c1c1c" role="img" aria-label="Cowboy hat icon"/>
      <!-- service shapes -->
      <ellipse cx="92" cy="212" rx="56" ry="26" fill="none" stroke="#fff" stroke-width="2.5"/>
      <path d="M200 190 V184 H310 V190 M200 234 V240 H310 V234" fill="none" stroke="#fff" stroke-width="2.5"/>
      <polygon points="382,188 480,188 431,238" fill="none" stroke="#fff" stroke-width="2.5"/>
      <!-- visit hexagons -->
      <line x1="70" y1="344" x2="440" y2="344" stroke="#fff" stroke-width="2"/>
      <g fill="#fff">
        <polygon points="60,330 80,330 90,344 80,358 60,358 50,344"/>
        <polygon points="130,330 150,330 160,344 150,358 130,358 120,344"/>
        <polygon points="200,330 220,330 230,344 220,358 200,358 190,344"/>
        <polygon points="270,330 290,330 300,344 290,358 270,358 260,344"/>
        <polygon points="340,330 360,330 370,344 360,358 340,358 330,344"/>
        <polygon points="410,330 430,330 440,344 430,358 410,358 400,344"/>
      </g>
      <g font-family="Ultra, serif" font-size="18" fill="#e8762c" text-anchor="middle">
        <text x="70" y="351">1</text><text x="140" y="351">2</text><text x="210" y="351">3</text>
        <text x="280" y="351">4</text><text x="350" y="351">5</text><text x="420" y="351">6</text>
      </g>
      <!-- extras corner brackets -->
      <g fill="none" stroke="#fff" stroke-width="2">
        <path d="M82 448 V438 H94 M154 438 H166 V448 M82 466 V476 H94 M154 476 H166 V466"/>
        <path d="M232 448 V438 H244 M388 438 H400 V448 M232 466 V476 H244 M388 476 H400 V466"/>
        <path d="M82 520 V510 H94 M154 510 H166 V520 M82 538 V548 H94 M154 548 H166 V538"/>
        <path d="M232 520 V510 H244 M388 510 H400 V520 M232 538 V548 H244 M388 548 H400 V538"/>
      </g>
    </svg>

    <div class="step" style="top:140px"><small>STEP 1</small><strong>CHOOSE YOUR SERVICE</strong></div>
    <div class="svc" style="left:36px;top:200px;width:112px;font-size:18px">COWBOY</div>
    <div class="svc" style="left:200px;top:184px;width:110px;font-size:18px"><small style="display:block;font-family:'Montserrat',sans-serif;font-size:10px;font-weight:600">LITTLE</small>COWBOY</div>
    <div class="svc" style="left:382px;top:190px;width:98px;font-size:17px">SHAVE</div>

    <div class="step" style="top:278px"><small>STEP 2</small><strong>CHOOSE YOUR VISITS</strong><small style="letter-spacing:2px">(IN WEEKS)</small></div>

    <div class="step" style="top:400px"><small>STEP 3</small><strong>CHOOSE YOUR EXTRAS</strong></div>
    <div class="extra" style="left:82px;top:440px;width:84px;font-size:17px"><small>FREE</small>BEER</div>
    <div class="extra" style="left:232px;top:440px;width:168px;font-size:17px"><small>UNLIMITED</small>NECK SHAVES</div>
    <div class="extra" style="left:82px;top:512px;width:84px;font-size:17px"><small>EYEBROW</small>WAX</div>
    <div class="extra" style="left:232px;top:518px;width:168px;font-size:18px">COLORADO</div>
  </section>

  <!-- Perks -->
  <div class="perks-title">
    <div class="the">THE</div>
    <div class="big">— PERKS —</div>
    <small>(INCLUDED WITH ALL MEMBERSHIPS)</small>
  </div>
  <section class="perks">
    <svg width="500" height="142" viewBox="0 0 500 142">
      <polyline points="100,2 30,2 2,30 2,140 498,140 498,30 470,2 400,2" fill="none" stroke="#1c1c1c" stroke-width="1.5"/>
    </svg>
    <ul>
      <li>Discounts on additional services, products &amp; drinks!</li>
      <li>Reduced rate for private parties &amp; after-hours events!</li>
      <li>Deals for friends &amp; referral bonuses for you!</li>
      <li>Additional specials, invitations &amp; access throughout the year!</li>
    </ul>
  </section>

</main>
</body>
</html>
```